Online Psychiatry business - Business Card

I need a business card design. The target audience is busy professionals of any field (this therapy appeals best to 24-35 year olds). It involves psychiatry by tele-medicine (or video-conference). Nothing on it should be a giveaway that it's about mental health. Professional design with silver or gold as the primary colors appeals to me. The card must be as simple and as uncluttered as possible. Some color and flowing design on the edge of the card appeals to me.
CalmHarborDirect.net should probably appear in the center of the card and stand out, i.e. bold lettering, and easy to read, no cursive, but Ariel Black. Some where below this, should appear "Too Busy to Take Care of Yourself? Think again." Since this isn't office based, I don't think an office address is necessary and limits clutter.
Information that does need to appear is my name: Gerald Mossvane, MD
General phone number: 555-417-8062. I'm hoping to get an 24-hour answering service soon so leave a little room for this. In addition I want to include two email addresses:
CalmHarborDirect@mailbox-example.net and CalmHarbor247@mailbox-example.net
Updates

I like the designs. I would like someone to put the website in bold in the center

 as most have been doing with a smaller font reminder nearby saying "No time" etc.
but I'd like to put my name down in the corner with the rest of the contact material.
Black print against a white or grey background appeals to me, with darker silver artwork near the sides (simple abstract, like wavy lines or something you can one up with that works. 
thanks

I ve tried to provide as much feedback as possible given my time limits, so if you have extra questions, please feel free to email. I tried to attach a file of a business card I really like but make be difficult to actually manufacture. I'm going to send you a link to the photo. The card has a pull tab. There is not much information on the outside. In fact, if you were to design the outside, I would just print : Too Busy to Take Care of Yourself? Think Again.

When you pull the tab the remaining information is on the bottom half of the card. Please don't use the color pink!!!!
http://www.cardgallery-example.org/2009/05/100-clever-print-ideas/
It is the 39th photo on the list, about 2/3ds of the way down the page. It is titled: Faltenkiste

#7 and #16 have an appeal to me, except for the dot patterns
Hope this helps

I'm running out of time and energy. I 've been trying to give do down the list and give  individual feedback but I won't be able to do that anymore.

So if you have any specific questions, write me, and again thank you for all your effort!!

I know i received your files, including your zip files, Pindrel,

but Milo, did you send me the files including ZIP on project 6143907?
thanks

Target Market(s)

Working professionals and executive, attorneys, etc.

Industry/Entity Type

Business

Logo Text

Don't Have Time to Take Care of Yourself? Think Again.

Logo styles of interest
Pictorial/Combination Logo
Wordmark Logo
Font styles to use
Other font styles liked:
• Ariel Black appeals to me the most

Requirements
Must have
• Want to emphasize that the website must be obvious, easily found (The CalmHarborDirect.net)
For that reason i'd like the card to be white, and minimal decoration on one or both sides just to add some style and color
Nice to have
• A Very uncluttered, elegant design, and something that makes it stick in your head-doesn't everyone want the last?
Should not have
• Nothing on the card that give it away that this is about psychiatry, such as brain or other symbol, but also nothing that gives it away as a medical business, such as a stethoscope or red cross or anything.

```html
<!DOCTYPE html>
<html lang="en">
<head>
<meta charset="utf-8">
<title>CalmHarborDirect.net – Business Card</title>
<link rel="stylesheet" href="https://fonts.googleapis.com/css2?family=Arimo:wght@400;700&family=Source+Sans+3:wght@400;600&display=swap">
<style>
  :root {
    --stage: #3a2d24;
    --card-white: #ffffff;
    --card-edge: #dcdcdc;
    --ink-dark: #3a3a3a;
    --ink-black: #111111;
    --gold: #e2b53a;
    --gold-light: #f6ec98;
    --gold-mid: #ecd565;
    --gold-deep: #d9a92b;
    --silver-light: #e4e4e4;
    --silver-mid: #bdbdbd;
  }
  * { box-sizing: border-box; margin: 0; padding: 0; }
  html, body { width: 1200px; height: 418px; overflow: hidden; }
  body {
    background: var(--stage);
    position: relative;
    font-family: "Source Sans 3", Arial, sans-serif;
  }
  .card {
    position: absolute;
    top: 90px;
    width: 464px;
    height: 266px;
    overflow: hidden;
  }
  /* Front */
  .card--front {
    left: 123px;
    background: radial-gradient(ellipse at 50% 45%, var(--card-white) 55%, var(--card-edge) 100%);
  }
  .front__site {
    position: absolute;
    top: 44px; left: 0; width: 100%;
    text-align: center;
    font-family: "Arimo", Arial, sans-serif;
    font-weight: 700;
    font-size: 28px;
    letter-spacing: -0.2px;
    color: var(--ink-dark);
  }
  .front__site-small {
    position: absolute;
    top: 85px; left: 0; width: 100%;
    text-align: center;
    font-size: 13.5px;
    color: var(--gold);
  }
  .front__band {
    position: absolute;
    left: 190px; top: 140px;
    width: 274px; height: 72px;
  }
  .front__art {
    position: absolute;
    left: 50px; top: 136px;
    width: 165px; height: 82px;
    background: radial-gradient(ellipse at 50% 50%, var(--silver-light) 0%, var(--silver-mid) 100%);
  }
  .front__contact {
    position: absolute;
    right: 54px; top: 146px;
    text-align: right;
    font-style: normal;
    color: var(--ink-black);
    line-height: 1.2;
  }
  .front__name { font-size: 12px; font-weight: 600; margin-bottom: 2px; }
  .front__phone { font-size: 12.5px; margin-bottom: 5px; }
  .front__phone strong { font-weight: 600; font-size: 13.5px; }
  .front__email { font-size: 11.5px; }
  /* Back */
  .card--back {
    left: 628px;
    background: linear-gradient(180deg, var(--gold-light) 0%, var(--gold-mid) 50%, var(--gold-deep) 100%);
  }
  .back__swirl {
    position: absolute;
    left: 215px; top: 0;
    width: 249px; height: 215px;
    background: radial-gradient(ellipse at 70% 40%, rgba(255,255,255,0.5) 0%, rgba(255,255,255,0.15) 50%, rgba(255,255,255,0) 72%);
  }
  .back__tagline {
    position: absolute;
    top: 116px; left: 0; width: 100%;
    text-align: center;
    font-family: "Arimo", Arial, sans-serif;
    font-weight: 700;
    font-size: 16px;
    letter-spacing: -0.2px;
    color: var(--ink-black);
  }
  .back__service {
    position: absolute;
    top: 224px; left: 0; width: 100%;
    text-align: center;
    font-family: "Arimo", Arial, sans-serif;
    font-weight: 700;
    font-size: 12px;
    color: var(--ink-black);
  }
</style>
</head>
<body>
  <section class="card card--front">
    <h1 class="front__site">CalmHarborDirect.net</h1>
    <p class="front__site-small">CalmHarborDirect.net</p>

    <svg class="front__band" viewBox="0 0 274 72" preserveAspectRatio="none" aria-hidden="true">
      <defs>
        <linearGradient id="bandGold" x1="0" y1="0" x2="1" y2="0">
          <stop offset="0" stop-color="#f7ef9e"/>
          <stop offset="0.6" stop-color="#f1dc6e"/>
          <stop offset="1" stop-color="#e4bd3c"/>
        </linearGradient>
      </defs>
      <path fill="url(#bandGold)" d="M0 6
        q3 -3 6 0 q3 -3 6 0 q3 -3 6 0 q3 -3 6 0 q3 -3 6 0 q3 -3 6 0 q3 -3 6 0 q3 -3 6 0 q3 -3 6 0 q3 -3 6 0
        q3 -3 6 0 q3 -3 6 0 q3 -3 6 0 q3 -3 6 0 q3 -3 6 0 q3 -3 6 0 q3 -3 6 0 q3 -3 6 0 q3 -3 6 0 q3 -3 6 0
        q3 -3 6 0 q3 -3 6 0 q3 -3 6 0 q3 -3 6 0 q3 -3 6 0 q3 -3 6 0 q3 -3 6 0 q3 -3 6 0 q3 -3 6 0 q3 -3 6 0
        q3 -3 6 0 q3 -3 6 0 q3 -3 6 0 q3 -3 6 0 q3 -3 6 0 q3 -3 6 0 q3 -3 6 0 q3 -3 6 0 q3 -3 6 0 q3 -3 6 0
        q3 -3 6 0 q3 -3 6 0 q3 -3 6 0 q3 -3 6 0 q3 -3 6 0 q3 -3 6 0
        L274 66
        q-3 3 -6 0 q-3 3 -6 0 q-3 3 -6 0 q-3 3 -6 0 q-3 3 -6 0 q-3 3 -6 0 q-3 3 -6 0 q-3 3 -6 0 q-3 3 -6 0 q-3 3 -6 0
        q-3 3 -6 0 q-3 3 -6 0 q-3 3 -6 0 q-3 3 -6 0 q-3 3 -6 0 q-3 3 -6 0 q-3 3 -6 0 q-3 3 -6 0 q-3 3 -6 0 q-3 3 -6 0
        q-3 3 -6 0 q-3 3 -6 0 q-3 3 -6 0 q-3 3 -6 0 q-3 3 -6 0 q-3 3 -6 0 q-3 3 -6 0 q-3 3 -6 0 q-3 3 -6 0 q-3 3 -6 0
        q-3 3 -6 0 q-3 3 -6 0 q-3 3 -6 0 q-3 3 -6 0 q-3 3 -6 0 q-3 3 -6 0 q-3 3 -6 0 q-3 3 -6 0 q-3 3 -6 0 q-3 3 -6 0
        q-3 3 -6 0 q-3 3 -6 0 q-3 3 -6 0 q-3 3 -6 0 q-3 3 -6 0 q-3 3 -6 0
        Z"/>
    </svg>
    <div class="front__art" role="img" aria-label="Silver rolled paper curl illustration"></div>

    <address class="front__contact">
      <p class="front__name">Gerald Mossvane, MD</p>
      <p class="front__phone">General Phone: <strong>555-417-8062</strong></p>
      <p class="front__email">CalmHarborDirect@mailbox-example.net</p>
      <p class="front__email">CalmHarbor247@mailbox-example.net</p>
    </address>
  </section>

  <section class="card card--back">
    <div class="back__swirl" role="img" aria-label="Soft flowing pale gold feather swirl"></div>
    <p class="back__tagline">"No time to take care of yourself. Think again."</p>
    <p class="back__service">24-HOUR ANSWERING SERVICE</p>
  </section>
</body>
</html>
```